Professional Baby Bottle Bank Print Design

We need a baby bottle design that is 4.25" wide x 2.28" tall with a maximum of 6 colors (white is counted as a color).

The bottle design needs to be fun but professional. Bottles with cartoon images on it will be rejected immediately.

The bottle design wraps around the bottle. See examples here: https://vel.quin/cat/BabyBottles/HarlowBottles/5

Minimum font size is 10pt.

The bottle design must have the following text on it:
Main Text: Love them both
Paragraph text: Our ministry’s aim is to not only save unborn babies, but to provide love, support, and life-saving resources for vulnerable women in our community. By filling this bottle with cash, checks, and spare coins and returning it on collection day, you are truly saving and changing lives!
Optional text: Thank you!

We are including an example file and a template file. You do NOT have to use the template - but your file has to be the exact size mentioned. If you don't design as well as our sample, please don't waste our time by spamming us with hundreds of designs. We will ban design houses that spam us with designs that are more layouts (and not well designed).

Please note - white is a color. You don't have to do a box - but anything you don't make white will be see-through.

We will take the winners of this contest to a survey with the customers. We may choose two and edit the text of one slightly to be different. We must know the fonts used.

No gradients unless they are half-toned with relatively big sized dots.

Target Market(s)

Church Attendees coming from a Pregnancy Center

Industry/Entity Type

Religious Christian Churches

Requirements
Must have
• Professional, great palette, wording as described.
Nice to have
• Integrated design across the whole space with areas for text (no text all the way across)
Should not have
• Cartoon figures; elements shoved together that don't go together (i.e. - actually design something)

```html
<!DOCTYPE html>
<html lang="en">
<head>
<meta charset="utf-8">
<title>Love Them Both – Bottle Wrap</title>
<link rel="stylesheet" href="https://fonts.googleapis.com/css2?family=Abril+Fatface&family=Lilita+One&family=Source+Sans+3:wght@400;500&display=swap">
<style>
  :root {
    --orange: #f39325;
    --orange-soft: #f5a04a;
    --teal: #138aa3;
    --sky: #dbeff6;
    --bubble: #b9e0ea;
    --cream: #fdf6ef;
    --white: #ffffff;
  }
  * { margin: 0; padding: 0; box-sizing: border-box; }
  html, body {
    width: 1200px; height: 1000px; overflow: hidden;
    background: var(--white);
  }
  .wrap-label {
    position: absolute; left: 122px; top: 245px;
    width: 956px; height: 510px;
    background: var(--cream);
    overflow: hidden;
  }
  .backdrop { position: absolute; inset: 0; }
  .mother-child {
    position: absolute; left: 30px; top: 125px;
    width: 360px; height: 385px;
    border-radius: 180px 180px 0 0;
    background: linear-gradient(160deg, var(--teal) 0%, var(--teal) 45%, var(--orange) 100%);
    opacity: 0.9;
  }
  .headline {
    position: absolute; left: 434px; top: 32px;
    font-family: "Abril Fatface", "Playfair Display", serif;
    font-size: 84px; line-height: 69px;
    letter-spacing: -1px;
  }
  .headline .love { color: var(--orange); display: block; }
  .headline .them, .headline .both { color: var(--teal); display: block; }
  .mission {
    position: absolute; right: 44px; top: 266px;
    width: 520px;
    font-family: "Source Sans 3", "Myriad Pro", sans-serif;
    font-size: 23px; line-height: 30.5px;
    color: var(--teal); text-align: right;
  }
  .thanks-badge {
    position: absolute; left: 377px; top: 368px;
    width: 112px; height: 112px; border-radius: 50%;
    background: var(--teal);
    outline: 3px dotted var(--teal); outline-offset: -1px;
    display: flex; align-items: center; justify-content: center;
    font-family: "Lilita One", "Fredoka", sans-serif;
    color: var(--white); font-size: 26px; line-height: 24px;
    text-align: center;
  }
</style>
</head>
<body>
  <section class="wrap-label">
    <svg class="backdrop" width="956" height="510" viewBox="0 0 956 510" aria-hidden="true">
      <circle cx="118" cy="401" r="343" fill="var(--sky)"/>
      <circle cx="1026" cy="-56" r="308" fill="var(--sky)"/>
      <g fill="none" stroke="var(--bubble)" stroke-width="2.5">
        <circle cx="612" cy="44" r="5"/>
        <circle cx="675" cy="58" r="8"/>
        <circle cx="703" cy="45" r="10"/>
        <circle cx="715" cy="74" r="5"/>
        <circle cx="687" cy="80" r="3"/>
        <circle cx="743" cy="72" r="4"/>
        <circle cx="798" cy="73" r="13"/>
        <circle cx="797" cy="28" r="10"/>
        <circle cx="857" cy="46" r="7"/>
        <circle cx="913" cy="27" r="5"/>
        <circle cx="893" cy="4" r="17"/>
        <circle cx="922" cy="82" r="28"/>
        <circle cx="633" cy="80" r="10"/>
      </g>
      <path d="M795 150 C 775 110, 740 100, 712 110 C 680 125, 695 170, 720 190 C 760 220, 820 222, 830 225 M 795 150 C 790 100, 805 75, 825 75 C 850 75, 862 115, 858 150 C 855 180, 842 200, 835 218"
            fill="none" stroke="var(--orange)" stroke-width="8" stroke-linecap="round" stroke-linejoin="round"/>
    </svg>

    <div class="mother-child" role="img" aria-label="Illustration of a mother tenderly holding her baby"></div>

    <h1 class="headline">
      <span class="love">Love</span>
      <span class="them">Them</span>
      <span class="both">Both</span>
    </h1>

    <p class="mission">
      Our ministry’s aim is to not only save unborn<br>
      babies, but to provide love, support, and<br>
      life-saving resources for vulnerable women<br>
      in our community. By filling this bottle<br>
      with cash, checks, and spare coins and<br>
      returning it on collection day, you are<br>
      truly saving and changing lives!
    </p>

    <div class="thanks-badge">Thank<br>You!</div>
  </section>
</body>
</html>
```